Varnik Holdings — Business Card Design Brief
Overview
Design a double-sided business card for Varnik Holdings that highlights our two service arms: Varnik Communications (telecommunications) and Varnik Energy (business energy solutions). The card should feel smart and stand out when handed to clients.

Objectives
Showcase our areas of specialty clearly.
Reflect the overall Varnik / Varnik Holdings brand while acknowledging both arms.
Explore using both logos (Communications + Energy) or one unified logo, depending on the design.

Deliverables
One double-sided business card design (front + back).

Content & Copy
Front (preferred): Logo: Varnik / Varnik Holdings
Descriptor: Business Communications | Business Energy
Back:My contact details and company details
Core products: Business Mobile • Telephony • Internet • Business Energy Solutions

Brand & Visual Direction
We have a group logo currently tailored more toward telecoms, plus a separate Varnik Energy logo.
Please explore layouts that use both logos or just one, whichever works best.
Color: I wouldn't mind seeing an option using our the Blue/Purple gradient from our website (varnik-example.co.uk), but also open to non-gradient approaches and other colours..

Overall look: Smart, modern, and distinctive.
Format & Print Specs
Double-sided business card format. (Use a standard size

Must-Haves
Front: Varnik wording or Varnik Holdings wording with atleast 1 logo also on front “Business Communications | Business Energy.”

Back: Contact + company details and core products.
A design that stands out while remaining professional.

Nice-to-Have Options
A gradient version using our site’s Blue/Purple gradient.
A non-gradient version.
A dual-logo treatment versus a single-logo treatment.

Thanks
Owen

```html
<!DOCTYPE html>
<html lang="en">
<head>
<meta charset="utf-8">
<title>Varnik Holdings — Business Card</title>
<link rel="stylesheet" href="https://fonts.googleapis.com/css2?family=Roboto:wght@400;500;700&display=swap">
<style>
  :root {
    --page: #e6e6e6;
    --card: #ffffff;
    --navy: #1b1a6b;
    --text: #4a4a4a;
    --green: #3aa51d;
    --blue-start: #0c5fd6;
    --blue-end: #0a94dc;
    --green-start: #44ab12;
    --green-end: #b8cc00;
    --comm-mark: #1478e0;
    --energy-mark: #4fb21a;
    --white: #ffffff;
  }
  * { box-sizing: border-box; margin: 0; padding: 0; }
  html, body { width: 1200px; height: 1200px; overflow: hidden; }
  body {
    background: var(--page);
    font-family: "Roboto", Arial, sans-serif;
    position: relative;
  }
  .card {
    position: absolute;
    left: 265px;
    width: 690px;
    height: 394px;
    overflow: hidden;
  }
  .card-front { top: 158px; background: var(--card); }
  .card-back { top: 654px; display: flex; }

  /* Front */
  .holder { position: absolute; left: 40px; top: 44px; }
  .holder-name { font-size: 26px; font-weight: 700; color: var(--navy); letter-spacing: 0.5px; line-height: 1; }
  .holder-title { font-size: 16px; color: var(--green); margin-top: 6px; }
  .address { position: absolute; left: 40px; top: 178px; font-size: 16px; color: var(--text); line-height: 21px; }
  .contacts { position: absolute; left: 40px; top: 241px; list-style: none; font-size: 16px; color: var(--text); }
  .contacts li { display: flex; align-items: center; height: 20.5px; }
  .contacts svg { width: 14px; height: 14px; margin-right: 10px; fill: var(--navy); }
  .website { position: absolute; left: 40px; top: 311px; font-size: 16px; color: var(--text); }

  .wordmark { display: flex; align-items: center; gap: 10px; font-weight: 700; }
  .wordmark .dot { border-radius: 50%; flex: none; }
  .front-marks { position: absolute; left: 460px; top: 0; width: 200px; }
  .front-marks .wordmark { position: absolute; left: 0; font-size: 34px; color: var(--navy); }
  .front-marks .dot { width: 36px; height: 36px; }
  .mark-comm { top: 70px; }
  .mark-comm .dot { background: var(--comm-mark); }
  .mark-energy { top: 230px; }
  .mark-energy .dot { background: var(--energy-mark); }

  .products { position: absolute; left: 0; bottom: 0; width: 100%; height: 36px; display: flex; color: var(--white); font-size: 17px; }
  .products-comm { width: 417px; background: var(--blue-start); display: flex; align-items: center; padding-left: 40px; gap: 14px; }
  .products-energy { flex: 1; background: var(--green); display: flex; align-items: center; padding-left: 17px; border-left: 1px solid var(--white); }

  /* Back */
  .side { height: 100%; display: flex; flex-direction: column; align-items: center; justify-content: center; color: var(--white); }
  .side-comm { width: 352px; background: linear-gradient(90deg, var(--blue-start), var(--blue-end)); }
  .side-energy { flex: 1; background: linear-gradient(90deg, var(--green-start), var(--green-end)); }
  .side .wordmark { font-size: 50px; color: var(--white); letter-spacing: 1px; }
  .side .dot { width: 48px; height: 48px; border: 5px solid var(--white); }
  .descriptor { margin-top: 22px; font-size: 16px; }
  .side-energy .descriptor { letter-spacing: 3px; }
</style>
</head>
<body>
  <section class="card card-front" aria-label="Card front">
    <div class="holder">
      <p class="holder-name">MARTA LINDQVIST</p>
      <p class="holder-title">President</p>
    </div>
    <p class="address">214 Alder Court<br>Fernvale, Canada 612</p>
    <ul class="contacts">
      <li><svg viewBox="0 0 24 24" aria-hidden="true"><path d="M6.6 10.8a15 15 0 0 0 6.6 6.6l2.2-2.2a1 1 0 0 1 1-.25 11.4 11.4 0 0 0 3.6.57 1 1 0 0 1 1 1V20a1 1 0 0 1-1 1A17 17 0 0 1 3 4a1 1 0 0 1 1-1h3.5a1 1 0 0 1 1 1c0 1.25.2 2.45.57 3.57a1 1 0 0 1-.25 1z"/></svg>555-210-4471</li>
      <li><svg viewBox="0 0 24 24" aria-hidden="true"><path d="M7 1h10a2 2 0 0 1 2 2v18a2 2 0 0 1-2 2H7a2 2 0 0 1-2-2V3a2 2 0 0 1 2-2zm0 3v15h10V4z"/></svg>555-210-8836</li>
      <li><svg viewBox="0 0 24 24" aria-hidden="true"><path d="M2 5h20v14H2zm2 2v.5l8 5 8-5V7zm0 2.8V17h16V9.8l-8 5z"/></svg>info@varnik-example.com</li>
    </ul>
    <p class="website">www.varnik-example.com</p>

    <div class="front-marks">
      <div class="wordmark mark-comm"><span class="dot"></span>VARNIK</div>
      <div class="wordmark mark-energy"><span class="dot"></span>VARNIK</div>
    </div>

    <div class="products">
      <div class="products-comm"><span>Business Mobile</span><span>•</span><span>Telephony</span><span>•</span><span>Internet</span></div>
      <div class="products-energy">Business Energy Solutions</div>
    </div>
  </section>

  <section class="card card-back" aria-label="Card back">
    <div class="side side-comm">
      <div class="wordmark"><span class="dot"></span>VARNIK</div>
      <p class="descriptor">BUSINESS COMMUNICATIONS</p>
    </div>
    <div class="side side-energy">
      <div class="wordmark"><span class="dot"></span>VARNIK</div>
      <p class="descriptor">BUSINESS ENERGY</p>
    </div>
  </section>
</body>
</html>
```